Varnick Fundraising E-mail Campaign

I intend to use Constant Contact to send donors 4 separate e-mail messages with pictures, text and a hot link, “Give to Restore Marlowe.” E-mails will spaced about 3 days apart. I would like the first e-mail to go out on Monday, December 17. The e-mail campaign is part of a board match annual appeal fundraising campaign for a not for profit sleep away Christian camp. Our hope is to raise $40,000.00+

Target Market(s)

Members in Constant Contact list

Colors

Designer to choose colors to be used in the design.

Requirements
Must have
• E- mail recipient must be able to access hot link

```html
<!DOCTYPE html>
<html lang="en">
<head>
<meta charset="utf-8">
<title>Varnick Fundraising E-mail Campaign</title>
<link href="https://fonts.googleapis.com/css2?family=Arimo:wght@400;700&display=swap" rel="stylesheet">
<style>
:root{
  --stage:#a9cb86;
  --bar:#0b7d3b;
  --brand:#0a6f35;
  --text:#1e7b47;
  --link:#e0482b;
  --alert:#e8402a;
  --frame:#9fc97c;
  --paper:#ffffff;
  --hill:#22a23a;
  --water:#27b0dd;
  --ribbon:#d81f26;
  --give:#d9232e;
}
*{box-sizing:border-box;margin:0;padding:0}
html,body{width:1200px;height:787px;overflow:hidden;background:var(--stage)}
body{position:relative;font-family:"Arimo",Arial,sans-serif;color:var(--text)}
.email{position:absolute;top:34px;width:265px;background:var(--paper);overflow:hidden}
.email--1{left:31px;height:508px}
.email--2{left:321px;height:732px}
.email--3{left:616px;height:609px}
.email--4{left:911px;height:480px}
.email__bar{height:12px;background:var(--bar);color:#fff;font-size:6px;font-weight:700;text-align:center;line-height:12px}
.email__brand{position:absolute;top:20px;left:0;right:0;display:flex;justify-content:center;align-items:center;gap:5px;color:var(--brand);font-size:13px;letter-spacing:.5px}
.email__brand i{width:10px;height:10px;background:var(--brand);display:block}
.photo{position:absolute;left:14px;width:237px;border:2px solid var(--frame)}
.copy{position:absolute;left:11px;right:11px;font-size:6.2px;line-height:1.38}
.copy--lg{font-size:7px;line-height:1.36}
.copy p+p{margin-top:6px}
.copy ul{margin:8px 0 0 20px;list-style:none}
.copy li::before{content:"•";color:var(--frame);margin-left:-9px;margin-right:5px}
.cta{position:absolute;left:0;right:0;text-align:center;font-size:8.6px;line-height:1.15}
.cta a{color:var(--link)}
.cta b{color:var(--brand)}
.btn{position:absolute;left:88px;width:88px;height:21px;background:var(--bar);color:#fff;font-size:8.5px;line-height:21px;text-align:center;text-decoration:none}
.btn--red{background:var(--give)}
.contact{position:absolute;left:5px;font-size:5.4px;line-height:1.4}
.landscape{position:absolute;left:0;bottom:0;width:265px;height:42px;background:linear-gradient(to bottom,rgba(34,162,58,0) 0%,var(--hill) 35%,var(--hill) 60%,var(--water) 100%)}
.alert{position:absolute;left:0;right:0;text-align:center;color:var(--alert);font-size:11.2px}
.hero{position:absolute;left:0;top:12px;width:265px;height:74px}
.hero__art{position:absolute;left:0;top:0;width:140px;height:74px;background:linear-gradient(to bottom,#ffffff 0%,#bfe3b0 45%,var(--hill) 75%,var(--water) 100%)}
.hero__name{position:absolute;right:9px;top:22px;font-size:27px;color:var(--brand);letter-spacing:.5px}
.ribbon{position:absolute;left:0;top:86px;width:265px;height:13px;background:var(--ribbon)}
</style>
</head>
<body>

<article class="email email--1">
  <div class="email__bar">view in a browser</div>
  <div class="email__brand"><i></i>VARNICK</div>
  <div class="photo" style="top:46px;height:158px;background:linear-gradient(135deg,#3a3a33,#1c1f1a 60%,#6b6a5a)" role="img" aria-label="Smiling teenage camper wearing a cap indoors by a window"></div>
  <div class="copy" style="top:220px">
    <p>Unfortunately, too many of our children spend more time playing video games and watching TV than having fun playing outdoors. Mateo, an average 13-year-old, spends about 300 hours a year playing video games. That's because many parents wonder where they can find a safe and engaging place for their children to experience nature and engaging activities with peers</p>
    <p>The Board of Directors of Varnick Presbyterian Camp and Conference Center decided to create a space that is safe, meaningful and fun by issuing the Revitalize Camp Marlowe Lake Matching Challenge.<br>They will match on a 1: 1 basis every dollar given or pledged to the campaign by December 31 up to $20,000.00.</p>
    <p>Please help us create a space where children like Mateo experience nature, connect with other children and have fun! Take advantage of the Revitalize Camp Marlowe Lake Matching Challenge and donate today</p>
  </div>
  <p class="cta" style="top:360px">Click <a href="#">here</a> &nbsp;to Give to Restore Marlowe and choose<br><b>"Restore Marlowe"</b></p>
  <a class="btn" href="#" style="top:389px">Donate Now</a>
  <p class="contact" style="top:426px">Contact:<br>48 Marlowe Lake Road Varnick, NY 12999<br>Phone: 555-014-2200 Fax: 555-014-2201<br>E-Mail: info@varnickcamp.org</p>
  <div class="landscape" role="img" aria-label="Illustrated green hills, a lake and a tree"></div>
</article>

<article class="email email--2">
  <div class="email__bar">view in a browser</div>
  <div class="email__brand"><i></i>VARNICK</div>
  <div class="photo" style="top:46px;height:158px;background:linear-gradient(135deg,#3f6a2c,#6f8f4a 50%,#2d4a22)" role="img" aria-label="Three children crouching by a stream in the woods"></div>
  <div class="copy copy--lg" style="top:220px">
    <p>A revitalized Marlowe Lake can do so much for children like Nora. Research shows that playing outdoors will (1) enhance Nora's ability to learn, (2) stimulates Nora's creativity, (3) increases Nora's sense of well-being and (4) improve Nora's social skills. Research also shows that youth who attend Christian summer camp grow to interpret all of life through a lens of faith.</p>
  </div>
  <div class="photo" style="top:282px;height:156px;background:linear-gradient(135deg,#6f9a4a,#a08070 50%,#4d7a32)" role="img" aria-label="Two smiling campers hugging at a picnic table"></div>
  <div class="copy copy--lg" style="top:455px">
    <p>You can help us provide Nora and children like her by taking advantage of the Revitalize Camp Marlowe Lake Matching Challenge</p>
    <ul>
      <li>$100.00 will buy: material for a picnic table</li>
      <li>$250.00 will buy: materials to improve the tent frames</li>
      <li>$500.00 will buy: materials to repair the bath house roof</li>
      <li>$1,000.00 will buy: a new tent to replace one damaged by tornado</li>
      <li>$5,000.00 will buy: half the roofing material for Marlowe Dining Hall</li>
    </ul>
    <p style="margin-top:12px">If you haven't done so, please donate today.</p>
  </div>
  <p class="cta" style="top:586px">Click <a href="#">here</a> &nbsp;to Give to Restore Marlowe and choose<br><b>"Restore Marlowe"</b></p>
  <a class="btn" href="#" style="top:614px">Donate Now</a>
  <p class="contact" style="top:650px">Contact:<br>48 Marlowe Lake Road Varnick, NY 12999<br>Phone: 555-014-2200 Fax: 555-014-2201<br>E-Mail: info@varnickcamp.org</p>
  <div class="landscape" role="img" aria-label="Illustrated green hills, a lake and a tree"></div>
</article>

<article class="email email--3">
  <div class="email__bar">view in a browser</div>
  <div class="email__brand"><i></i>VARNICK</div>
  <div class="photo" style="top:46px;height:158px;background:linear-gradient(135deg,#6a4a32,#3a88c0 45%,#e08a78 75%,#5a3f2c)" role="img" aria-label="Two smiling girl campers indoors in a cabin"></div>
  <div class="copy copy--lg" style="top:220px">
    <p>Last chance to take advantage of the matching challenge! Double your impact! Every gift is matched dollar for dollar up to 20,000!</p>
  </div>
  <div class="photo" style="top:254px;height:155px;background:linear-gradient(135deg,#2f5e22,#5e9a3c 50%,#24481a)" role="img" aria-label="Campers hiking in a line through a green forest"></div>
  <p class="alert" style="top:428px">If you haven't done so, please donate today.</p>
  <p class="cta" style="top:462px">Click <a href="#">here</a> &nbsp;to Give to Restore Marlowe and choose<br><b>"Restore Marlowe"</b></p>
  <a class="btn" href="#" style="top:490px">Donate Now</a>
  <p class="contact" style="top:526px">Contact:<br>48 Marlowe Lake Road Varnick, NY 12999<br>Phone: 555-014-2200 Fax: 555-014-2201<br>E-Mail: info@varnickcamp.org</p>
  <div class="landscape" role="img" aria-label="Illustrated green hills, a lake and a tree"></div>
</article>

<article class="email email--4">
  <div class="email__bar">DONATE NOW</div>
  <div class="hero">
    <div class="hero__art" role="img" aria-label="Illustrated green hill with a tree by a lake"></div>
    <span class="hero__name">VARNICK</span>
  </div>
  <div class="ribbon" role="img" aria-label="Red holiday ribbon with a bow"></div>
  <div class="photo" style="top:106px;left:17px;width:234px;height:130px;background:linear-gradient(135deg,#5a4a3a,#c8a84a 45%,#3a2e26)" role="img" aria-label="Three cheerful campers posing together"></div>
  <div class="copy copy--lg" style="top:266px">
    <p>Only one more day to take advantage of the Revitalize Camp Marlowe Lake Matching Challenge by making a year-end tax-deductible gift to Varnick Presbyterian Camp and Conference Center. This is the perfect time to make a gift that will help all our children have a transformative experience. If you have not done so, please donate now.</p>
  </div>
  <p class="cta" style="top:332px">Click <a href="#">here</a> &nbsp;to Give to Restore Marlowe and choose<br><b>"Restore Marlowe"</b></p>
  <a class="btn btn--red" href="#" style="top:362px">Donate Now</a>
  <p class="contact" style="top:398px">Contact:<br>48 Marlowe Lake Road Varnick, NY 12999<br>Phone: 555-014-2200 Fax: 555-014-2201<br>E-Mail: info@varnickcamp.org</p>
  <div class="landscape" role="img" aria-label="Illustrated green hills, a lake and a decorated holiday tree"></div>
</article>

</body>
</html>
```